Graphics for New Online Software

Looking at a designer to design a UI/UX Interface for an Online Events Platform (just JPEG) and some corresponding images for a website content (i.e. features etc)

Deliverables:
1x User Interface Design for the Platform (refer to attachment)
5-6x Feature Listing Images (refer to attachment)

Target Market(s)

Technology, Online Users Etc

Industry/Entity Type

Software Developer

Number of Pages Required

1 page

Font styles to use
Sans Serif

Colors
34a7d8
0493ce
3176b5
85acd3

Requirements
Must have
• Looks like a well built software - examples:
https://gravelmoor.io/
https://quintaro.com/

All the images should look very professional, as though you are using it on the online platform itself.
Nice to have
• Refer to attached "Feature Listing" and Logo

```html
<!DOCTYPE html>
<html lang="en">
<head>
<meta charset="utf-8">
<title>Venuora – Event Platform Screens</title>
<link href="https://fonts.googleapis.com/css2?family=Poppins:wght@400;500;600;700&display=swap" rel="stylesheet">
<style>
:root{
  --bg-top:#1663c4;
  --bg-bottom:#7d9fd1;
  --sidebar:#1c1e33;
  --sidebar-line:#262941;
  --active:#2b3cf1;
  --main:#f1f1f3;
  --white:#ffffff;
  --accent:#36b1f6;
  --heading-blue:#2534e6;
  --button:#1f6ec6;
  --ink:#1e2030;
  --muted:#6b6e7c;
  --bubble:#eef0f4;
}
*{box-sizing:border-box;margin:0;padding:0}
html,body{width:1200px;height:2834px;overflow:hidden}
body{
  font-family:'Poppins',sans-serif;color:var(--ink);
  background:linear-gradient(180deg,var(--bg-top) 0%,#3f7fcb 35%,var(--bg-bottom) 100%);
  position:relative;
}
.screen{position:absolute;left:111px;width:965px;background:var(--main);box-shadow:0 6px 24px rgba(0,0,20,.25);overflow:visible}
.screen--event{top:127px;height:887px}
.screen--stage{top:1081px;height:1027px}
.screen--rewards{top:2170px;height:536px}

.topbar{position:absolute;left:0;top:0;width:100%;height:73px;background:var(--white);display:flex;align-items:center}
.brand{position:absolute;left:14px;top:18px;font-weight:700;font-size:28px;letter-spacing:-.5px;color:var(--ink)}
.user{position:absolute;left:440px;top:19px;display:flex;align-items:center;gap:12px;font-size:11px}
.user .avatar{width:34px;height:34px;border-radius:50%;background:linear-gradient(135deg,#7d8a99,#3b4553)}
.settings{position:absolute;left:605px;top:26px;display:flex;align-items:center;gap:8px;font-size:13px}
.duration{position:absolute;left:714px;top:27px;font-size:13px}

.sidebar{position:absolute;left:0;top:73px;width:194px;bottom:0;background:var(--sidebar)}
.nav{list-style:none}
.nav li{position:relative;height:44px;display:flex;align-items:center;border-bottom:1px solid var(--sidebar-line);font-size:13px;color:#fff}
.nav li:first-child{height:46px}
.nav .ico{width:53px;height:100%;display:flex;align-items:center;justify-content:center;border-right:1px solid var(--sidebar-line)}
.nav .label{padding-left:13px}
.nav li.is-active{background:var(--active);border-bottom-color:var(--active)}
.nav li.is-active::after{content:"";position:absolute;right:-22px;top:0;border-top:23px solid transparent;border-bottom:23px solid transparent;border-left:22px solid var(--active)}
.nav li.is-active .ico{border-right-color:var(--active)}
.nav li:nth-child(3) .label{font-size:12px}

.footer{position:absolute;left:194px;right:0;text-align:center;font-size:12px;color:#2a2c3a}

.section-title{position:absolute;font-weight:600;font-size:22px;left:236px;top:98px}
.photo{position:absolute;width:138px;height:150px;display:flex;align-items:flex-end;justify-content:center;padding-bottom:12px;color:#fff;font-size:12px;font-weight:500;text-shadow:0 1px 2px rgba(0,0,0,.5)}
.photo.p1{background:linear-gradient(160deg,#c9ccd0,#4d5460)}
.photo.p2{background:linear-gradient(160deg,#2a98a8,#17616f)}
.photo.p3{background:linear-gradient(160deg,#6c5a4a,#1e2027)}
.photo.p4{background:linear-gradient(160deg,#3a6d97,#b8862a)}
.photo.p5{background:linear-gradient(160deg,#5f86b0,#1d2d4a)}
.photo.p6{background:linear-gradient(160deg,#78828b,#cfc8c0)}
.photo.p7{background:linear-gradient(160deg,#8e9296,#333845)}
.photo.p8{background:linear-gradient(160deg,#e7e7ea,#233a78)}
.photo.p9{background:linear-gradient(160deg,#6f9a56,#2d3e55)}
.photo.p10{background:linear-gradient(160deg,#aab2b8,#3a3c44)}
.photo.p11{background:linear-gradient(160deg,#4f8f95,#1a1e25)}
.photo.p12{background:linear-gradient(160deg,#4a4d55,#14161c)}

.card{position:absolute;background:var(--white);box-shadow:0 2px 6px rgba(0,0,0,.14)}
.card-head{position:relative;height:50px;border-bottom:1px solid #e4e4e8;display:flex;align-items:center;padding-left:56px;font-weight:600;font-size:18px;color:var(--heading-blue)}
.card-head svg{position:absolute;left:0;top:0}
.card-image{height:134px;background:linear-gradient(120deg,#e7b25a 0%,#9a6a34 45%,#3d3a36 100%)}
.card-text{font-size:11px;line-height:18px;color:#2a2c3a;text-align:center;padding:16px 14px 0}
.btn{display:block;margin:14px auto 0;width:126px;height:29px;border-radius:15px;background:var(--button);color:#fff;font-size:12px;font-weight:600;text-align:center;line-height:29px;letter-spacing:.5px}
.prog-item{padding:0 20px}
.prog-item h4{font-size:11.5px;font-weight:600;letter-spacing:.2px;display:flex;align-items:center;gap:6px;margin-bottom:4px}
.prog-item h4::after{content:"";width:5px;height:5px;border-right:2px solid var(--accent);border-top:2px solid var(--accent);transform:rotate(45deg)}
.prog-item p{font-size:11px;line-height:16px;color:#2a2c3a}

.video{position:absolute;display:flex;align-items:center;justify-content:center}
.video.main{background:linear-gradient(135deg,#5a6878 0%,#2d4f72 45%,#1e2a3a 100%)}
.video.desk{background:linear-gradient(135deg,#2a3850,#0f1826)}
.video.cafe{background:linear-gradient(135deg,#6b4a2f,#1d1b1f)}

.chat-user{display:flex;align-items:center;padding:0 16px;height:38px;font-size:11px;font-weight:600;border-bottom:1px solid #eee}
.chat-user .dot{width:6px;height:6px;border-radius:50%;background:#2ec4a0;margin-left:8px}
.chat-user .tools{margin-left:auto;display:flex;gap:10px;align-items:center}
.msg{position:absolute;display:flex;align-items:center;gap:10px}
.msg .face{width:26px;height:26px;border-radius:50%;background:linear-gradient(135deg,#b7bcc4,#4a4f5a)}
.msg .bubble{height:24px;border-radius:12px;padding:0 15px;font-size:9px;line-height:24px;background:var(--bubble);color:#333}
.msg.out .bubble{background:var(--button);color:#fff}
.chat-input{position:absolute;left:8px;right:8px;bottom:10px;height:42px;border:1px solid #e6e6ea;border-radius:4px;display:flex;align-items:center;padding:0 6px 0 14px;font-size:9px;color:#999}
.chat-input .send{width:28px;height:28px;border-radius:50%;background:var(--button);display:flex;align-items:center;justify-content:center}

.reward-tile{position:absolute;top:136px;width:201px;height:140px;background:var(--accent);color:#fff;text-align:center;font-weight:600;font-size:15px;line-height:19px;letter-spacing:.4px;padding-top:26px}
.reward-tile svg{display:block;margin:0 auto 6px}
.reward-line{position:absolute;text-align:center}
</style>
</head>
<body>

<!-- Event info screen -->
<section class="screen screen--event">
  <header class="topbar">
    <div class="brand">Venuora</div>
    <div class="user"><span class="avatar" role="img" aria-label="User profile photo"></span>Tavi Renald</div>
    <div class="settings"><svg width="16" height="16" viewBox="0 0 16 16"><circle cx="8" cy="8" r="5.5" fill="none" stroke="#555" stroke-width="1.4" stroke-dasharray="3 1.3"/><circle cx="8" cy="8" r="2.2" fill="none" stroke="#555" stroke-width="1.3"/></svg>Settings</div>
    <div class="duration">Event Duration (Remaining 02:54)</div>
  </header>
  <aside class="sidebar">
    <ul class="nav">
      <li class="is-active"><span class="ico"><svg width="16" height="16" viewBox="0 0 16 16"><rect x="1.5" y="3" width="13" height="11.5" fill="none" stroke="#fff" stroke-width="1.5"/><rect x="1.5" y="3" width="13" height="3" fill="#fff"/><rect x="4" y="1" width="1.6" height="3.5" fill="#fff"/><rect x="10.4" y="1" width="1.6" height="3.5" fill="#fff"/></svg></span><span class="label">Event Info</span></li>
      <li><span class="ico"><svg width="16" height="16" viewBox="0 0 16 16"><path d="M15 1 1 7.5l5 1.5 1.5 5L15 1z" fill="#fff"/></svg></span><span class="label">Stage</span></li>
      <li><span class="ico"><svg width="18" height="16" viewBox="0 0 18 16"><rect x="5" y="1" width="7" height="6" fill="none" stroke="#fff" stroke-width="1.5"/><rect x="1" y="8" width="7" height="6" fill="none" stroke="#fff" stroke-width="1.5"/><rect x="9" y="8" width="7" height="6" fill="none" stroke="#fff" stroke-width="1.5"/></svg></span><span class="label">Breakouts</span></li>
      <li><span class="ico"><svg width="16" height="16" viewBox="0 0 16 16"><path d="M8 2 1 8h2v6h4v-4h2v4h4V8h2z" fill="#fff"/></svg></span><span class="label">Booths</span></li>
      <li><span class="ico"><svg width="18" height="14" viewBox="0 0 18 14"><rect x="3" y="1" width="12" height="8.5" fill="none" stroke="#fff" stroke-width="1.5"/><rect x="1" y="11" width="16" height="2" fill="#fff"/></svg></span><span class="label">Virtual Exhibition</span></li>
      <li><span class="ico"><svg width="18" height="18" viewBox="0 0 24 24"><path d="M12 2l3 6.5 7 .8-5.2 4.8 1.5 7L12 17.6 5.7 21.1l1.5-7L2 9.3l7-.8z" fill="#fff"/></svg></span><span class="label">Rewards</span></li>
    </ul>
  </aside>

  <h2 class="section-title">Speakers</h2>
  <div class="photo p1" role="img" aria-label="Speaker portrait" style="left:236px;top:150px">John Doe</div>
  <div class="photo p2" role="img" aria-label="Speaker portrait" style="left:388px;top:150px">John Doe</div>
  <div class="photo p3" role="img" aria-label="Speaker portrait" style="left:540px;top:150px">John Doe</div>
  <div class="photo p4" role="img" aria-label="Speaker portrait" style="left:236px;top:315px">John Doe</div>
  <div class="photo p5" role="img" aria-label="Speaker portrait" style="left:388px;top:315px">John Doe</div>
  <div class="photo p6" role="img" aria-label="Speaker portrait" style="left:540px;top:315px">John Doe</div>
  <div class="photo p7" role="img" aria-label="Speaker portrait" style="left:236px;top:481px">John Doe</div>
  <div class="photo p8" role="img" aria-label="Speaker portrait" style="left:388px;top:481px">John Doe</div>
  <div class="photo p9" role="img" aria-label="Speaker portrait" style="left:540px;top:481px">John Doe</div>
  <div class="photo p10" role="img" aria-label="Speaker portrait" style="left:236px;top:646px">John Doe</div>
  <div class="photo p11" role="img" aria-label="Speaker portrait" style="left:388px;top:646px">John Doe</div>
  <div class="photo p12" role="img" aria-label="Speaker portrait" style="left:540px;top:646px">John Doe</div>

  <article class="card" style="left:707px;top:113px;width:221px;height:360px">
    <div class="card-head"><svg width="40" height="50" viewBox="0 0 40 50"><polygon points="0,0 20,0 40,25 20,50 0,50" fill="var(--accent)"/></svg>Agenda</div>
    <div class="card-image" role="img" aria-label="Man working on a laptop in a sunlit office"></div>
    <p class="card-text">Sed ut perspiciatis unde omnis iste natus error sit voluptatem accusantium doloremque latium, totam rem aperiam, eaque ipsa quae ab illo inventore</p>
    <span class="btn">Learn more</span>
  </article>

  <article class="card" style="left:707px;top:493px;width:221px;height:302px">
    <div class="card-head"><svg width="40" height="50" viewBox="0 0 40 50"><polygon points="0,0 20,0 40,25 20,50 0,50" fill="var(--accent)"/></svg>Programming</div>
    <div class="prog-item" style="margin-top:24px"><h4>NEMO ENIM IPSAM</h4><p>Sed ut perspiciatis unde omnis iste natus error sit voluptatem accusantium</p></div>
    <div class="prog-item" style="margin-top:17px"><h4>NEMO ENIM IPSAM</h4><p>Sed ut perspiciatis unde omnis iste natus error sit voluptatem accusantium</p></div>
    <span class="btn" style="margin:20px 0 0 21px">Learn more</span>
  </article>

  <p class="footer" style="top:838px">©2020 Venuora All Rights Reserved.</p>
</section>

<!-- Stage screen -->
<section class="screen screen--stage">
  <header class="topbar">
    <div class="brand">Venuora</div>
    <div class="user"><span class="avatar" role="img" aria-label="User profile photo"></span>Tavi Renald</div>
    <div class="settings"><svg width="16" height="16" viewBox="0 0 16 16"><circle cx="8" cy="8" r="5.5" fill="none" stroke="#555" stroke-width="1.4" stroke-dasharray="3 1.3"/><circle cx="8" cy="8" r="2.2" fill="none" stroke="#555" stroke-width="1.3"/></svg>Settings</div>
    <div class="duration">Event Duration (Remaining 02:54)</div>
  </header>
  <aside class="sidebar">
    <ul class="nav">
      <li><span class="ico"><svg width="16" height="16" viewBox="0 0 16 16"><rect x="1.5" y="3" width="13" height="11.5" fill="none" stroke="#fff" stroke-width="1.5"/><rect x="1.5" y="3" width="13" height="3" fill="#fff"/><rect x="4" y="1" width="1.6" height="3.5" fill="#fff"/><rect x="10.4" y="1" width="1.6" height="3.5" fill="#fff"/></svg></span><span class="label">Event Info</span></li>
      <li class="is-active"><span class="ico"><svg width="16" height="16" viewBox="0 0 16 16"><path d="M15 1 1 7.5l5 1.5 1.5 5L15 1z" fill="#fff"/></svg></span><span class="label">Stage</span></li>
      <li><span class="ico"><svg width="18" height="16" viewBox="0 0 18 16"><rect x="5" y="1" width="7" height="6" fill="none" stroke="#fff" stroke-width="1.5"/><rect x="1" y="8" width="7" height="6" fill="none" stroke="#fff" stroke-width="1.5"/><rect x="9" y="8" width="7" height="6" fill="none" stroke="#fff" stroke-width="1.5"/></svg></span><span class="label">Breakouts</span></li>
      <li><span class="ico"><svg width="16" height="16" viewBox="0 0 16 16"><path d="M8 2 1 8h2v6h4v-4h2v4h4V8h2z" fill="#fff"/></svg></span><span class="label">Booths</span></li>
      <li><span class="ico"><svg width="18" height="14" viewBox="0 0 18 14"><rect x="3" y="1" width="12" height="8.5" fill="none" stroke="#fff" stroke-width="1.5"/><rect x="1" y="11" width="16" height="2" fill="#fff"/></svg></span><span class="label">Virtual Exhibition</span></li>
      <li><span class="ico"><svg width="18" height="18" viewBox="0 0 24 24"><path d="M12 2l3 6.5 7 .8-5.2 4.8 1.5 7L12 17.6 5.7 21.1l1.5-7L2 9.3l7-.8z" fill="#fff"/></svg></span><span class="label">Rewards</span></li>
    </ul>
  </aside>

  <div class="video main" role="img" aria-label="Video: team meeting around a holographic globe" style="left:236px;top:113px;width:441px;height:249px">
    <svg width="38" height="28" viewBox="0 0 38 28"><rect x="1.5" y="1.5" width="35" height="25" rx="6" fill="none" stroke="#fff" stroke-width="3"/><polygon points="15,8 25,14 15,20" fill="#fff"/></svg>
  </div>
  <div class="video desk" role="img" aria-label="Video: developer at multiple monitors" style="left:236px;top:371px;width:216px;height:144px">
    <svg width="38" height="28" viewBox="0 0 38 28"><rect x="1.5" y="1.5" width="35" height="25" rx="6" fill="none" stroke="#fff" stroke-width="3"/><polygon points="15,8 25,14 15,20" fill="#fff"/></svg>
  </div>
  <div class="video cafe" role="img" aria-label="Video: video call on a laptop in a cafe" style="left:462px;top:371px;width:215px;height:144px">
    <svg width="38" height="28" viewBox="0 0 38 28"><rect x="1.5" y="1.5" width="35" height="25" rx="6" fill="none" stroke="#fff" stroke-width="3"/><polygon points="15,8 25,14 15,20" fill="#fff"/></svg>
  </div>

  <article class="card" style="left:707px;top:113px;width:221px;height:403px">
    <div class="card-head"><svg width="40" height="50" viewBox="0 0 40 50"><polygon points="0,0 20,0 40,25 20,50 0,50" fill="var(--accent)"/></svg>CHAT</div>
    <div class="chat-user">John Doe<span class="dot"></span>
      <span class="tools">
        <svg width="12" height="12" viewBox="0 0 12 12"><path d="M2 1h3l1 3-1.5 1a7 7 0 0 0 2.5 2.5L8 6l3 1v3a1 1 0 0 1-1 1A9 9 0 0 1 1 2a1 1 0 0 1 1-1z" fill="#bbb"/></svg>
        <svg width="12" height="12" viewBox="0 0 12 12"><circle cx="6" cy="6" r="5" fill="none" stroke="#bbb" stroke-width="1.5"/><circle cx="6" cy="5" r="1.8" fill="#bbb"/></svg>
        <svg width="4" height="12" viewBox="0 0 4 12"><circle cx="2" cy="2" r="1.3" fill="#bbb"/><circle cx="2" cy="6" r="1.3" fill="#bbb"/><circle cx="2" cy="10" r="1.3" fill="#bbb"/></svg>
      </span>
    </div>
    <div class="msg" style="left:18px;top:118px"><span class="face" role="img" aria-label="Participant avatar"></span><span class="bubble">Nemo enim ipsam volupta</span></div>
    <div class="msg out" style="left:19px;top:160px"><span class="bubble">Nemo enim ipsam volupta</span><span class="face" role="img" aria-label="Participant avatar"></span></div>
    <div class="msg" style="left:18px;top:208px"><span class="face" role="img" aria-label="Participant avatar"></span><span class="bubble">Nemo enim ipsam volupta</span></div>
    <div class="msg out" style="left:19px;top:250px"><span class="bubble">Nemo enim ipsam volupta</span><span class="face" role="img" aria-label="Participant avatar"></span></div>
    <div class="msg" style="left:18px;top:297px"><span class="face" role="img" aria-label="Participant avatar"></span><span class="bubble">Nemo enim ipsam volupta</span></div>
    <div class="chat-input">Type your message ...
      <svg style="margin-left:auto;margin-right:8px" width="8" height="12" viewBox="0 0 8 12"><path d="M6 3v6a2 2 0 0 1-4 0V2.5a1.3 1.3 0 0 1 2.6 0V8" fill="none" stroke="#bbb" stroke-width="1"/></svg>
      <span class="send"><svg width="14" height="12" viewBox="0 0 14 12"><path d="M1 1l12 5-12 5 2-5z" fill="#fff"/></svg></span>
    </div>
  </article>

  <article class="card" style="left:236px;top:552px;width:220px;height:358px">
    <div class="card-head"><svg width="40" height="50" viewBox="0 0 40 50"><polygon points="0,0 20,0 40,25 20,50 0,50" fill="var(--accent)"/></svg>Agenda</div>
    <div class="card-image" role="img" aria-label="Man working on a laptop in a sunlit office"></div>
    <p class="card-text">Sed ut perspiciatis unde omnis iste natus error sit voluptatem accusantium doloremque latium, totam rem aperiam, eaque ipsa quae ab illo inventore</p>
    <span class="btn">Learn more</span>
  </article>

  <article class="card" style="left:481px;top:552px;width:447px;height:358px">
    <div class="card-head"><svg width="40" height="50" viewBox="0 0 40 50"><polygon points="0,0 20,0 40,25 20,50 0,50" fill="var(--accent)"/></svg>Programming</div>
    <div style="display:grid;grid-template-columns:1fr 1fr;row-gap:18px;margin-top:28px;padding-left:6px">
      <div class="prog-item"><h4>NEMO ENIM IPSAM</h4><p>Sed ut perspiciatis unde omnis iste natus error sit voluptatem accusantium</p></div>
      <div class="prog-item"><h4>NEMO ENIM IPSAM</h4><p>Sed ut perspiciatis unde omnis iste natus error sit voluptatem accusantium</p></div>
      <div class="prog-item"><h4>NEMO ENIM IPSAM</h4><p>Sed ut perspiciatis unde omnis iste natus error sit voluptatem accusantium</p></div>
      <div class="prog-item"><h4>NEMO ENIM IPSAM</h4><p>Sed ut perspiciatis unde omnis iste natus error sit voluptatem accusantium</p></div>
      <div class="prog-item"><h4>NEMO ENIM IPSAM</h4><p>Sed ut perspiciatis unde omnis iste natus error sit voluptatem accusantium</p></div>
      <div class="prog-item"><h4>NEMO ENIM IPSAM</h4><p>Sed ut perspiciatis unde omnis iste natus error sit voluptatem accusantium</p></div>
    </div>
  </article>

  <p class="footer" style="top:962px">©2020 Venuora All Rights Reserved.</p>
</section>

<!-- Rewards screen -->
<section class="screen screen--rewards">
  <header class="topbar">
    <div class="brand">Venuora</div>
    <div class="user"><span class="avatar" role="img" aria-label="User profile photo"></span>Tavi Renald</div>
    <div class="settings"><svg width="16" height="16" viewBox="0 0 16 16"><circle cx="8" cy="8" r="5.5" fill="none" stroke="#555" stroke-width="1.4" stroke-dasharray="3 1.3"/><circle cx="8" cy="8" r="2.2" fill="none" stroke="#555" stroke-width="1.3"/></svg>Settings</div>
    <div class="duration">Event Duration (Remaining 02:54)</div>
  </header>
  <aside class="sidebar">
    <ul class="nav">
      <li><span class="ico"><svg width="16" height="16" viewBox="0 0 16 16"><rect x="1.5" y="3" width="13" height="11.5" fill="none" stroke="#fff" stroke-width="1.5"/><rect x="1.5" y="3" width="13" height="3" fill="#fff"/><rect x="4" y="1" width="1.6" height="3.5" fill="#fff"/><rect x="10.4" y="1" width="1.6" height="3.5" fill="#fff"/></svg></span><span class="label">Event Info</span></li>
      <li><span class="ico"><svg width="16" height="16" viewBox="0 0 16 16"><path d="M15 1 1 7.5l5 1.5 1.5 5L15 1z" fill="#fff"/></svg></span><span class="label">Stage</span></li>
      <li><span class="ico"><svg width="18" height="16" viewBox="0 0 18 16"><rect x="5" y="1" width="7" height="6" fill="none" stroke="#fff" stroke-width="1.5"/><rect x="1" y="8" width="7" height="6" fill="none" stroke="#fff" stroke-width="1.5"/><rect x="9" y="8" width="7" height="6" fill="none" stroke="#fff" stroke-width="1.5"/></svg></span><span class="label">Breakouts</span></li>
      <li><span class="ico"><svg width="16" height="16" viewBox="0 0 16 16"><path d="M8 2 1 8h2v6h4v-4h2v4h4V8h2z" fill="#fff"/></svg></span><span class="label">Booths</span></li>
      <li><span class="ico"><svg width="18" height="14" viewBox="0 0 18 14"><rect x="3" y="1" width="12" height="8.5" fill="none" stroke="#fff" stroke-width="1.5"/><rect x="1" y="11" width="16" height="2" fill="#fff"/></svg></span><span class="label">Virtual Exhibition</span></li>
      <li class="is-active"><span class="ico"><svg width="18" height="18" viewBox="0 0 24 24"><path d="M12 2l3 6.5 7 .8-5.2 4.8 1.5 7L12 17.6 5.7 21.1l1.5-7L2 9.3l7-.8z" fill="#fff"/></svg></span><span class="label">Rewards</span></li>
    </ul>
  </aside>

  <div class="card" style="left:235px;top:107px;width:692px;height:330px"></div>
  <div class="reward-tile" style="left:263px"><svg width="44" height="44" viewBox="0 0 44 44"><path d="M36 12A19 19 0 1 0 40 22" fill="none" stroke="#fff" stroke-width="3" stroke-linecap="round"/><path d="M13 21l8 8 19-19" fill="none" stroke="#fff" stroke-width="3" stroke-linecap="round" stroke-linejoin="round"/></svg>Visited Virtual<br>Exhibition</div>
  <div class="reward-tile" style="left:481px"><svg width="44" height="44" viewBox="0 0 44 44"><path d="M36 12A19 19 0 1 0 40 22" fill="none" stroke="#fff" stroke-width="3" stroke-linecap="round"/><path d="M13 21l8 8 19-19" fill="none" stroke="#fff" stroke-width="3" stroke-linecap="round" stroke-linejoin="round"/></svg>Joined<br>Breakout Room</div>
  <div class="reward-tile" style="left:697px"><svg width="44" height="44" viewBox="0 0 44 44"><path d="M36 12A19 19 0 1 0 40 22" fill="none" stroke="#fff" stroke-width="3" stroke-linecap="round"/><path d="M13 21l8 8 19-19" fill="none" stroke="#fff" stroke-width="3" stroke-linecap="round" stroke-linejoin="round"/></svg>Checked<br>out Booths</div>
  <p class="reward-line" style="left:235px;width:692px;top:307px;font-size:16px;font-weight:600">Total Points: 40</p>
  <p class="reward-line" style="left:235px;width:692px;top:335px;font-size:17px;font-weight:600">Collect Reward - Trigger Email/Link to 3rd Party App</p>
  <p class="reward-line" style="left:235px;width:692px;top:376px;font-size:9.5px">(Flash them a PROMO CODE/*Email will be given to you on how you can claim your prize)</p>

  <p class="footer" style="top:483px">©2020 Venuora All Rights Reserved.</p>
</section>

</body>
</html>
```